Beautify our counselling web application

I have a web application in development and at the moment it is very plain.
It has being developed with laravel and vue. I need a simple design for the user interface to make it look more sleek and professional. I will need someone who is able to code the design as part of the service. The app is very low-cost for voluntary and social enterprise services and we don't have a lot of money so I need someone who is just starting out or someone with a big heart.
I have uploaded current pages to show the contents.
I will tip for good work.

Target Market(s)

Counsellors and psychotherapists

Industry/Entity Type

SaaS

Font styles to use
Serif
Sans Serif

Colors
0054AA
0677BA
7BADD7
CADEEF
E8F1F8

Requirements
Must have
• Ability to code the design into the current site
Nice to have
• elegant, modern. cool, profession. nice examples include merovaultix.com quillbanter.com fenrodu.com
Should not have
• corny literal 90s icons, icons with more than one colour using primary colours

```html
<!DOCTYPE html>
<html lang="en">
<head>
<meta charset="utf-8">
<title>Counselling App – Screens</title>
<link href="https://fonts.googleapis.com/css2?family=Red+Hat+Display:wght@400;500;600;700&display=swap" rel="stylesheet">
<style>
:root{
  --board:#dedede;
  --surface:#f3f3f3;
  --white:#ffffff;
  --ink:#1c1c1c;
  --muted:#555555;
  --primary:#0054aa;
  --rule:#d6d6d6;
  --risk:#2bb673;
  --danger:#d9262c;
}
*{box-sizing:border-box;margin:0;padding:0}
html,body{width:1200px;height:699px;overflow:hidden}
body{background:var(--board);font-family:"Red Hat Display",Arial,sans-serif;color:var(--ink);position:relative}
.screen{position:absolute;width:534px;height:294px;background:var(--surface);box-shadow:0 0 2px rgba(0,0,0,.12);overflow:hidden}
.screen--dashboard{left:46px;top:38px}
.screen--caseload{left:607px;top:39px}
.screen--client{left:342px;top:358px}
.topbar{position:absolute;left:0;top:0;width:100%;height:43px;background:var(--white)}
.menu-icon{position:absolute;left:16px;top:18px;width:8px;height:9px;display:flex;justify-content:space-between}
.menu-icon span{width:1.8px;height:100%;background:var(--ink)}
.brand{position:absolute;left:52px;top:14px;font-size:9.5px;font-weight:600;color:var(--primary)}
.page-title{position:absolute;top:15px;font-size:8px;font-weight:600;transform:translateX(-50%);white-space:nowrap}
.tools{position:absolute;top:16px;left:466px;display:flex;gap:6px}
.tools svg{width:11px;height:11px}
.sidebar{position:absolute;left:10px;top:53px;width:86px;height:231px;background:var(--white);border-radius:6px;padding:13px 0 0 11px}
.sidebar li{list-style:none;font-size:6.8px;height:15.25px;line-height:8px}
.welcome{position:absolute;left:96px;top:59px;right:0;height:17px;background:var(--primary);color:var(--white);font-size:8px;font-weight:600;text-align:center;line-height:17px}
.block{position:absolute;left:110px}
.block h3{font-size:7px;font-weight:600}
.block p{font-size:6px;color:var(--muted);margin-top:2px}
.btn-primary{position:absolute;left:394px;top:89px;width:90px;height:18px;border-radius:9px;background:var(--primary);color:var(--white);font-size:6.8px;font-weight:600;text-align:center;line-height:18px}
.filterbar{position:absolute;left:102px;top:52px;width:390px;height:21px;background:var(--white);border-radius:4px;font-size:6px;color:var(--muted)}
.filterbar .filter{position:absolute;left:11px;top:7px}
.filterbar .divider{position:absolute;left:52px;top:5px;width:1px;height:11px;background:var(--rule)}
.filterbar .search{position:absolute;left:69px;top:7px;color:#a0a0a0}
.case-table{position:absolute;left:103px;top:79px;width:390px;height:201px;background:var(--white);border-radius:4px}
.case-table .head-rule{position:absolute;left:2px;right:0;top:23px;height:1px;background:var(--rule)}
.cell{position:absolute;font-size:4.2px;white-space:nowrap;transform:translateY(-50%)}
.cell.th{color:#333}
.cell.client{color:var(--primary)}
.dot{position:absolute;width:3.5px;height:3.5px;border-radius:50%;background:var(--risk);transform:translate(-50%,-50%)}
.tab{position:absolute;top:53px;height:19px;border-radius:3px;font-size:6.2px;text-align:center;line-height:17px;border:1px solid var(--primary);white-space:nowrap}
.tab--active{background:var(--primary);color:var(--white)}
.tab--outline{background:var(--white);color:#333}
.episode{position:absolute;left:103px;top:84px;width:391px;height:86px;background:var(--white);border-radius:4px}
.episode .rule{position:absolute;left:0;right:0;top:24px;height:1px;background:var(--rule)}
.episode .name{position:absolute;left:12px;top:9px;font-size:6.2px}
.episode .started{position:absolute;right:85px;top:9px;font-size:6.2px}
.episode .started b{font-weight:600}
.episode .chev{position:absolute;left:314px;top:10px;width:6px;height:5px}
.btn-danger{position:absolute;left:340px;top:5px;width:42px;height:14px;border-radius:2px;background:var(--danger);color:var(--white);font-size:5.4px;text-align:center;line-height:14px}
.chip{position:absolute;width:60px;height:14px;border-radius:3px;color:var(--white);font-size:6.2px;text-align:center;line-height:14px;white-space:nowrap}
</style>
</head>
<body>

<section class="screen screen--dashboard">
  <header class="topbar">
    <div class="menu-icon"><span></span><span></span><span></span></div>
    <div class="brand">Counselling App</div>
    <div class="page-title" style="left:265px">Dashboard</div>
    <div class="tools">
      <svg viewBox="0 0 12 12" fill="none" stroke="#1c1c1c" stroke-width="1"><circle cx="6" cy="6" r="5"/><path d="M4.5 4.6a1.5 1.5 0 1 1 2 1.4c-.4.2-.5.5-.5.9"/><circle cx="6" cy="8.7" r=".3" fill="#1c1c1c"/></svg>
      <svg viewBox="0 0 12 12" fill="none" stroke="#1c1c1c" stroke-width="1"><circle cx="6" cy="6" r="5"/><circle cx="6" cy="4.8" r="1.8"/><path d="M2.7 9.6c.8-1.3 2-2 3.3-2s2.5.7 3.3 2"/></svg>
      <svg viewBox="0 0 12 12" fill="none" stroke="#1c1c1c" stroke-width="1"><path d="M7 2.5V1.5H1.5v9H7v-1"/><path d="M4.5 6h6.5M9 4l2 2-2 2"/></svg>
    </div>
  </header>
  <ul class="sidebar">
    <li>Caseload</li><li>Calendar</li><li>Address Book</li><li>Users</li><li>Services</li><li>Clients</li><li>Audit</li><li>Monitoring</li><li>Templates</li>
  </ul>
  <div class="welcome">Welcome To Demo</div>
  <div class="block" style="top:94px"><h3>Notifications</h3><p>No Notifications</p></div>
  <div class="btn-primary">Create Notifications</div>
  <div class="block" style="top:137px"><h3>Today</h3><p>No Appointments!</p></div>
  <div class="block" style="top:181px"><h3>Reviews</h3><p>No Reviews</p></div>
</section>

<section class="screen screen--caseload">
  <header class="topbar">
    <div class="menu-icon"><span></span><span></span><span></span></div>
    <div class="brand">Counselling App</div>
    <div class="page-title" style="left:265px">Caseload</div>
    <div class="tools">
      <svg viewBox="0 0 12 12" fill="none" stroke="#1c1c1c" stroke-width="1"><circle cx="6" cy="6" r="5"/><path d="M4.5 4.6a1.5 1.5 0 1 1 2 1.4c-.4.2-.5.5-.5.9"/><circle cx="6" cy="8.7" r=".3" fill="#1c1c1c"/></svg>
      <svg viewBox="0 0 12 12" fill="none" stroke="#1c1c1c" stroke-width="1"><circle cx="6" cy="6" r="5"/><circle cx="6" cy="4.8" r="1.8"/><path d="M2.7 9.6c.8-1.3 2-2 3.3-2s2.5.7 3.3 2"/></svg>
      <svg viewBox="0 0 12 12" fill="none" stroke="#1c1c1c" stroke-width="1"><path d="M7 2.5V1.5H1.5v9H7v-1"/><path d="M4.5 6h6.5M9 4l2 2-2 2"/></svg>
    </div>
  </header>
  <ul class="sidebar">
    <li>Caseload</li><li>Calendar</li><li>Address Book</li><li>Users</li><li>Services</li><li>Clients</li><li>Audit</li><li>Monitoring</li><li>Templates</li>
  </ul>
  <div class="filterbar">
    <span class="filter">Filter &#8964;</span>
    <span class="divider"></span>
    <span class="search">Search</span>
  </div>
  <div class="case-table">
    <div class="head-rule"></div>
    <span class="cell th" style="left:16px;top:12px">Risk</span>
    <span class="cell th" style="left:39px;top:12px">Alerts</span>
    <span class="cell th" style="left:63px;top:12px">Client</span>
    <span class="cell th" style="left:105px;top:12px">ID</span>
    <span class="cell th" style="left:128px;top:12px">Service</span>
    <span class="cell th" style="left:168px;top:12px">Therapist</span>
    <span class="cell th" style="left:201px;top:12px">Date of Referral</span>
    <span class="cell th" style="left:254px;top:12px">First Contact</span>
    <span class="cell th" style="left:301px;top:12px">Previous Episode</span>
    <span class="cell th" style="left:358px;top:12px">Contact</span>

    <span class="dot" style="left:20px;top:37px"></span>
    <span class="cell client" style="left:63px;top:37px">Colin Marsh</span>
    <span class="cell" style="left:105px;top:37px">002</span>
    <span class="cell" style="left:128px;top:37px">Demo Service 1</span>
    <span class="cell" style="left:168px;top:37px">Dale</span>
    <span class="cell" style="left:201px;top:37px">05-07-2022</span>
    <span class="cell" style="left:254px;top:37px">20-09-2022</span>
    <span class="cell" style="left:358px;top:37px">&#9656; Total: 3</span>

    <span class="dot" style="left:20px;top:56px"></span>
    <span class="cell client" style="left:63px;top:56px">Nigel Fairley</span>
    <span class="cell" style="left:105px;top:56px">003</span>
    <span class="cell" style="left:128px;top:56px">Demo Service 1</span>
    <span class="cell" style="left:168px;top:56px">Dale</span>
    <span class="cell" style="left:201px;top:56px">13-07-2022</span>
    <span class="cell" style="left:254px;top:56px">20-09-2022</span>
    <span class="cell" style="left:358px;top:56px">&#9656; Total: 2</span>

    <span class="dot" style="left:20px;top:75px"></span>
    <span class="cell client" style="left:62px;top:75px">Hannah Corley</span>
    <span class="cell" style="left:105px;top:75px">004</span>
    <span class="cell" style="left:128px;top:75px">Demo Service 1</span>
    <span class="cell" style="left:168px;top:75px">Dale</span>
    <span class="cell" style="left:201px;top:75px">19-08-2022</span>
    <span class="cell" style="left:254px;top:75px">20-09-2022</span>
    <span class="cell" style="left:358px;top:75px">&#9656; Total: 3</span>

    <span class="dot" style="left:20px;top:93px"></span>
    <span class="cell client" style="left:62px;top:93px">Lydia Frost</span>
    <span class="cell" style="left:105px;top:93px">005</span>
    <span class="cell" style="left:128px;top:93px">Demo Service 2</span>
    <span class="cell" style="left:168px;top:93px">Owen</span>
    <span class="cell" style="left:201px;top:93px">17-08-2022</span>
    <span class="cell" style="left:254px;top:93px">20-09-2022</span>
    <span class="cell" style="left:358px;top:93px">&#9656; Total: 3</span>

    <span class="cell client" style="left:62px;top:112px">Imogen Tallis</span>
    <span class="cell" style="left:105px;top:112px">006</span>
    <span class="cell" style="left:128px;top:112px">Demo Service 2</span>
    <span class="cell" style="left:168px;top:112px">Owen</span>
    <span class="cell" style="left:201px;top:112px">23-08-2022</span>
    <span class="cell" style="left:254px;top:112px">20-09-2022</span>
    <span class="cell" style="left:303px;top:112px">29-09-2022</span>
    <span class="cell" style="left:358px;top:112px">&#9656; Total: 0</span>

    <span class="dot" style="left:20px;top:130px"></span>
    <span class="cell client" style="left:62px;top:130px">Eleanor Whitcombe</span>
    <span class="cell" style="left:105px;top:130px">007</span>
    <span class="cell" style="left:128px;top:130px">Demo Service 2</span>
    <span class="cell" style="left:168px;top:130px">Owen</span>
    <span class="cell" style="left:201px;top:130px">06-07-2022</span>
    <span class="cell" style="left:254px;top:130px">20-09-2022</span>
    <span class="cell" style="left:358px;top:130px">&#9656; Total: 2</span>
  </div>
</section>

<section class="screen screen--client">
  <header class="topbar">
    <div class="menu-icon"><span></span><span></span><span></span></div>
    <div class="brand">Counselling App</div>
    <div class="page-title" style="left:262px">Caseload / Colin Marsh</div>
    <div class="tools">
      <svg viewBox="0 0 12 12" fill="none" stroke="#1c1c1c" stroke-width="1"><circle cx="6" cy="6" r="5"/><path d="M4.5 4.6a1.5 1.5 0 1 1 2 1.4c-.4.2-.5.5-.5.9"/><circle cx="6" cy="8.7" r=".3" fill="#1c1c1c"/></svg>
      <svg viewBox="0 0 12 12" fill="none" stroke="#1c1c1c" stroke-width="1"><circle cx="6" cy="6" r="5"/><circle cx="6" cy="4.8" r="1.8"/><path d="M2.7 9.6c.8-1.3 2-2 3.3-2s2.5.7 3.3 2"/></svg>
      <svg viewBox="0 0 12 12" fill="none" stroke="#1c1c1c" stroke-width="1"><path d="M7 2.5V1.5H1.5v9H7v-1"/><path d="M4.5 6h6.5M9 4l2 2-2 2"/></svg>
    </div>
  </header>
  <ul class="sidebar">
    <li>Caseload</li><li>Calendar</li><li>Address Book</li><li>Users</li><li>Services</li><li>Clients</li><li>Audit</li><li>Monitoring</li><li>Templates</li>
  </ul>
  <div class="tab tab--active" style="left:109px;width:54px">Workspace &#8963;</div>
  <div class="tab tab--active" style="left:169px;width:64px">Client Information</div>
  <div class="tab tab--outline" style="left:240px;width:56px">Client Progress</div>
  <div class="tab tab--outline" style="left:301px;width:49px">Payments</div>

  <div class="episode">
    <span class="name">Episode 1</span>
    <span class="started"><b>Started:</b> Wed Sep 14 2022</span>
    <svg class="chev" viewBox="0 0 6 5" fill="none" stroke="#1c1c1c" stroke-width="1"><path d="M.5 4 3 1.3 5.5 4"/></svg>
    <div class="btn-danger">End Episode</div>
    <div class="rule"></div>
    <div class="chip" style="left:10px;top:36px;background:#d0607a">Session Record</div>
    <div class="chip" style="left:73px;top:36px;background:#b8703f">Assessment</div>
    <div class="chip" style="left:135px;top:36px;background:#b9a23a">Risk Management</div>
    <div class="chip" style="left:198px;top:36px;background:#5a9a3a">Treatment Plan</div>
    <div class="chip" style="left:261px;top:36px;background:#2f6b4b">Safeguarding</div>
    <div class="chip" style="left:324px;top:36px;background:#4a9ea0">Consent</div>
    <div class="chip" style="left:10px;top:58px;background:#5068a8">Questionnaire</div>
    <div class="chip" style="left:73px;top:58px;background:#4b3fb3">Document</div>
    <div class="chip" style="left:135px;top:58px;background:#4a2f6b">Non-clinical Note</div>
    <div class="chip" style="left:198px;top:58px;background:#9a7aa8">Summary</div>
    <div class="chip" style="left:261px;top:58px;background:#8a3a98">Timeline</div>
  </div>
</section>

</body>
</html>
```